Create the ONLY Supplement line for Male Entrepreneurs! (Verity Nine MD)

I need a label designed for a new supplement brand that I am launching.

There are five products so need a design that I can simply change the wording for each individual product

The brand name is called verity nine MD. The focus is male entrepreneurial health.

Target audience is men 35 to 55.

Concepts: the healthier you are in body the more money you will make in business.

Concept to copy: I want to make a clean minimalistic label mimicking Lansworth MD (google it and you'll see what I mean)

Target Market(s)

male entrepreneurs 35-55

Industry/Entity Type

Health Supplement

Colors

Designer to choose colors to be used in the design.

Requirements
Must have
• Modern classy design, similar to Lansworth MD.
Nice to have
• Highlight that the supplement is Doctor Approved.
Should not have
• No loud colors. Present it as high class.

```html
<!DOCTYPE html>
<html lang="en">
<head>
<meta charset="utf-8">
<title>Verity Nine MD – Dietary Supplement Label</title>
<link rel="stylesheet" href="https://fonts.googleapis.com/css2?family=Libre+Baskerville&family=Ubuntu:wght@400&display=swap">
<style>
  :root {
    --navy-bg: #073752;
    --brand-blue: #0b5283;
    --label-white: #ffffff;
    --text-grey: #5a5a5a;
    --pill-grey: #d3d3d5;
    --rule-grey: #c9c9c9;
    --ink-dark: #3d3d3d;
  }
  * { margin: 0; padding: 0; box-sizing: border-box; }
  html, body {
    width: 1200px;
    height: 2457px;
    overflow: hidden;
    background: var(--navy-bg);
  }
  .label {
    position: absolute;
    left: 194px;
    top: 790px;
    width: 812px;
    height: 878px;
    background: var(--label-white);
    font-family: "Ubuntu", sans-serif;
    overflow: hidden;
  }
  .label__top-band {
    position: absolute;
    left: 142px;
    top: 2px;
    width: 529px;
    height: 17px;
    background: var(--brand-blue);
  }
  .label__product-name {
    position: absolute;
    left: 136px;
    top: 102px;
    font-family: "Libre Baskerville", serif;
    font-size: 74px;
    line-height: 1;
    color: var(--brand-blue);
    white-space: nowrap;
    letter-spacing: -1px;
  }
  .label__maker {
    position: absolute;
    left: 138px;
    top: 560px;
    font-family: "Ubuntu", sans-serif;
    font-size: 22px;
    letter-spacing: 6px;
    color: var(--brand-blue);
    white-space: nowrap;
  }
  .label__approval-badge {
    position: absolute;
    left: 500px;
    top: 426px;
    width: 172px;
    height: 172px;
  }
  .label__type-band {
    position: absolute;
    left: 0;
    top: 622px;
    width: 512px;
    height: 63px;
    background: var(--brand-blue);
    color: var(--label-white);
    font-size: 31px;
    line-height: 63px;
    padding-left: 138px;
    white-space: nowrap;
  }
  .label__count-pill {
    position: absolute;
    left: 487px;
    top: 622px;
    width: 188px;
    height: 62px;
    border-radius: 31px;
    background: var(--pill-grey);
    border: 4px solid var(--label-white);
    color: var(--ink-dark);
    font-size: 27px;
    line-height: 54px;
    text-align: center;
    white-space: nowrap;
  }
  .label__ingredients {
    position: absolute;
    left: 138px;
    top: 690px;
    font-size: 14px;
    color: var(--text-grey);
    white-space: nowrap;
  }
  .label__rule {
    position: absolute;
    left: 138px;
    top: 722px;
    width: 318px;
    height: 1px;
    background: var(--rule-grey);
  }
  .label__pack-line {
    position: absolute;
    left: 138px;
    top: 728px;
    font-size: 21px;
    color: var(--brand-blue);
    white-space: nowrap;
  }
  .label__contents {
    position: absolute;
    left: 138px;
    top: 771px;
    font-size: 20px;
    color: var(--text-grey);
    white-space: nowrap;
  }
</style>
</head>
<body>
  <main class="label">
    <div class="label__top-band"></div>
    <h1 class="label__product-name">Verity Nine MD</h1>

    <p class="label__maker">HALDEN NUTRICEUTICALS</p>

    <svg class="label__approval-badge" viewBox="0 0 172 172" role="img" aria-label="Doctor approved seal">
      <circle cx="86" cy="86" r="84" fill="var(--brand-blue)"/>
      <circle cx="86" cy="86" r="56" fill="var(--label-white)"/>
      <circle cx="86" cy="86" r="49" fill="none" stroke="var(--brand-blue)" stroke-width="2"/>
    </svg>

    <div class="label__type-band">DIETARY SUPPLEMENT</div>
    <div class="label__count-pill">90 Softgels</div>

    <p class="label__ingredients">DMAE, Omega-3, Evening Primrose Oil</p>
    <div class="label__rule"></div>
    <p class="label__pack-line">Dietary Supplement. 90 packets</p>
    <p class="label__contents">Each packet contains: 3 softgels, 2 caplets and 2 capsules</p>
  </main>
</body>
</html>
```